Strategy plan/report for urban homeless shelter

Lay out a simple, 6-page report for a homeless shelter in San Jose, CA. Four statistics in the report need graphics. See style guide for color palette. EPS logo files included. Stock photography is available for use. Final strategy plan/report will be presented to board members, donors and foundations, so design needs to communicate need, concern (for the homeless) and hope for ending homelessness.

Target Market(s)

Tech executives who are board members and/or donors, as well as local foundations (e.g., the Wexmore Foundation, the Brindle Foundation).

Requirements
Must have
• Adhere to nonprofit's color palette (file attached).
• Graphical treatment of statistics.
• Agency's logo on front page. (file attached)
• Agency's url included: http://www.shelterlanevq.org
Nice to have
• White space is good.
Should not have
• Report will be printed so please do not use black or dark background.

```html
<!DOCTYPE html>
<html lang="en">
<head>
<meta charset="utf-8">
<title>Shelterlane Strategic Plan – Page 6</title>
<link href="https://fonts.googleapis.com/css2?family=Roboto+Condensed:ital,wght@0,700;1,400;1,700&family=Arimo:wght@400&display=swap" rel="stylesheet">
<style>
  :root{
    --backdrop:#eef1ee;
    --paper:#ffffff;
    --band-grey:#e4e4e4;
    --navy:#13243a;
    --ink:#1c1c1c;
    --yellow:#fdd01f;
  }
  *{margin:0;padding:0;box-sizing:border-box}
  html,body{width:1200px;height:1200px;overflow:hidden;background:var(--backdrop)}
  .page{
    position:absolute;left:158px;top:28px;width:884px;height:1144px;
    background:var(--paper);box-shadow:0 2px 10px rgba(0,0,0,.12);
    font-family:"Arimo",Arial,sans-serif;color:var(--ink);
  }
  .page-header{position:absolute;left:0;top:31px;width:100%;height:31px;background:var(--band-grey)}
  .brand{
    position:absolute;left:78px;top:6px;display:flex;align-items:center;gap:5px;
    font-family:"Roboto Condensed",sans-serif;font-weight:700;font-size:14px;color:var(--navy);
  }
  .brand-mark{width:11px;height:11px;background:var(--navy)}
  .page-number{
    position:absolute;left:770px;top:0;width:36px;height:31px;background:var(--navy);
    color:#fff;font-family:"Roboto Condensed",sans-serif;font-weight:700;font-size:20px;
    display:flex;align-items:center;justify-content:center;
  }
  .content{position:absolute;left:76px;top:186px;width:698px}
  .intro-note{font-family:"Roboto Condensed",sans-serif;font-style:italic;font-size:12px;line-height:15px;margin-bottom:30px}
  .goal-title{font-family:"Roboto Condensed",sans-serif;font-weight:700;font-style:italic;font-size:28px;color:var(--navy);line-height:32px;margin-bottom:6px}
  .goal-lead{font-family:"Roboto Condensed",sans-serif;font-weight:700;font-size:14px;line-height:18px;margin-bottom:16px}
  .objective{font-size:14px;line-height:18px;text-align:justify;margin-bottom:18px}
  .goal + .goal{margin-top:30px}
  .footnote{position:absolute;left:76px;top:930px;width:450px}
  .footnote-rule{width:248px;border-top:1px solid var(--ink);margin-bottom:6px}
  .footnote-text{font-family:"Roboto Condensed",sans-serif;font-style:italic;font-size:12px;padding-left:2px}
  .page-footer{
    position:absolute;left:0;top:1095px;width:100%;height:31px;background:var(--yellow);
    display:flex;align-items:center;justify-content:center;gap:6px;
    font-family:"Roboto Condensed",sans-serif;font-weight:700;font-size:20px;color:var(--navy);
  }
</style>
</head>
<body>
<div class="page">
  <header class="page-header">
    <div class="brand"><span class="brand-mark"></span>Shelterlane</div>
    <div class="page-number">6</div>
  </header>

  <main class="content">
    <p class="intro-note">In the 2013 census and survey of the homeless population in Santa Clara County, 64% of the people surveyed reported a mental illness diagnosis such as PTSD, depression or bipolar disorder.</p>

    <section class="goal">
      <h2 class="goal-title">Goal 3</h2>
      <p class="goal-lead">Shelterlane will build on its Supportive Services and develop a best practice model to help people who struggle to stay housed.</p>
      <p class="objective">Y1. To better serve our community Shelterlane will create comprehensive case management model to ensure long-term permanent housing solutions.</p>
      <p class="objective">Y2.&nbsp; We will develop internal roles and responsibilities to expand our housing services model.</p>
      <p class="objective">Y3.&nbsp; We will publish our results and established procedures to assist other communities with their goal of helping people who struggle to stay housed.</p>
    </section>

    <section class="goal">
      <h2 class="goal-title">Goal 2</h2>
      <p class="goal-lead">Shelterlane will continue to build its financial and program resources to ensure its role in meeting our community's needs:</p>
      <p class="objective">Y1.&nbsp; Shelterlane will expand on its Medi-Cal certification to enrich programs and expand contract services to serve more clients;</p>
      <p class="objective">Y1.&nbsp; Expand awareness in philanthropic, public service, and volunteer communities to support the long-term goals of Shelterlane.</p>
      <p class="objective">Y2.&nbsp; Create a cohesive property management business segment to build financial capacity with enhanced client services.</p>
    </section>
  </main>

  <aside class="footnote">
    <div class="footnote-rule"></div>
    <p class="footnote-text">Civic Survey Group, 2013 Santa Clara County Homeless Census and Survey</p>
  </aside>

  <footer class="page-footer"><span class="brand-mark"></span>Shelterlane</footer>
</div>
</body>
</html>
```